Fernhollow Air Business Card Design

Design new, 2 sides, business cards for a residential and light commercial heating, air conditioning contractor.

Target Market(s)

Homeowners, small businesses

Industry/Entity Type

Business

Contact Information for Business Card

Dominic Westerhall
Phone - 862-415-2736
Email
Address - PO box 518
Brightwater NJ 07912
Website - www.HarborBreezeLLC.example

Requirements
Must have
• logo, company colors, standard size with no die cut, so I can use nova stamp

```html
<!DOCTYPE html>
<html lang="en">
<head>
<meta charset="utf-8">
<title>Fernhollow Air Business Card</title>
<link rel="stylesheet" href="https://fonts.googleapis.com/css2?family=Open+Sans:ital,wght@0,400;0,600;0,700;1,400&display=swap">
<style>
  :root {
    --backdrop: #8c7151;
    --card: #ffffff;
    --card-shade: #e9e9e9;
    --maroon: #a3273b;
    --maroon-dark: #86192c;
    --orange: #e48a1e;
    --ink: #4d4d4d;
    --on-band: #ffffff;
  }
  * { box-sizing: border-box; margin: 0; padding: 0; }
  html, body { width: 1200px; height: 843px; overflow: hidden; }
  body {
    background: var(--backdrop);
    font-family: "Open Sans", Arial, sans-serif;
    color: var(--ink);
    position: relative;
  }
  .card {
    position: absolute;
    top: 267px;
    width: 540px;
    height: 309px;
    background: linear-gradient(180deg, var(--card) 55%, var(--card-shade) 100%);
    box-shadow: 0 6px 18px rgba(0,0,0,0.35);
    overflow: hidden;
  }
  .card--brand { left: 40px; }
  .card--contact { left: 620px; }

  .brand-name {
    display: flex;
    align-items: center;
    gap: 10px;
    font-weight: 700;
    color: var(--maroon);
    white-space: nowrap;
  }
  .brand-name .mark {
    width: 14px; height: 14px; border-radius: 50%;
    background: var(--orange);
    flex: none;
  }
  .card--brand .brand-name {
    position: absolute;
    left: 0; right: 0; top: 96px;
    justify-content: center;
    font-size: 44px;
  }
  .tagline {
    position: absolute;
    left: 0; right: 0; top: 190px;
    text-align: center;
    font-size: 15px;
    line-height: 1.35;
    font-weight: 600;
  }

  .band {
    position: absolute;
    left: 0; top: 40px;
    width: 100%; height: 96px;
    display: flex;
  }
  .band__main {
    flex: 0 0 78%;
    background: linear-gradient(100deg, var(--maroon) 0%, #b9455a 45%, var(--maroon-dark) 100%);
  }
  .band__accent { flex: 1; background: var(--orange); }
  .person {
    position: absolute;
    left: 26px; top: 54px;
    color: var(--on-band);
  }
  .person__name { font-size: 19px; font-weight: 600; letter-spacing: 0.5px; text-transform: uppercase; }
  .person__role { font-size: 13px; }
  .card--contact .brand-name {
    position: absolute;
    right: 18px; top: 72px;
    padding: 10px 14px;
    background: var(--card);
    border-radius: 6px;
    font-size: 22px;
  }

  .contact-list {
    position: absolute;
    left: 26px; top: 168px;
    list-style: none;
    font-size: 13.5px;
    line-height: 20px;
  }
  .contact-list li { display: flex; align-items: center; gap: 8px; }
  .contact-list svg { width: 14px; height: 14px; fill: var(--maroon); flex: none; }

  .address {
    position: absolute;
    right: 24px; bottom: 22px;
    text-align: right;
    font-size: 13.5px;
    line-height: 19px;
    letter-spacing: 0.4px;
  }
</style>
</head>
<body>

<section class="card card--brand" aria-label="Card back">
  <div class="brand-name"><span class="mark"></span>Fernhollow Air</div>
  <p class="tagline">Residential and light commercial heating<br>Air conditioning contractor</p>
</section>

<section class="card card--contact" aria-label="Card front">
  <div class="band"><div class="band__main"></div><div class="band__accent"></div></div>
  <div class="person">
    <p class="person__name">Dominic Westerhall</p>
    <p class="person__role">CEO/Founder</p>
  </div>
  <div class="brand-name"><span class="mark"></span>Fernhollow Air</div>

  <ul class="contact-list">
    <li><svg viewBox="0 0 16 16" aria-hidden="true"><path d="M3 1l3 3-2 2c1 2 4 5 6 6l2-2 3 3-2 2C7 15 1 9 1 3z"/></svg>862 415 2736</li>
    <li><svg viewBox="0 0 16 16" aria-hidden="true"><rect x="4" y="1" width="8" height="14" rx="1.5"/><rect x="5.5" y="3" width="5" height="8" fill="#fff"/></svg>862 415 2737</li>
    <li><svg viewBox="0 0 16 16" aria-hidden="true"><rect x="4" y="1" width="8" height="5"/><rect x="1" y="6" width="14" height="7" rx="1"/><rect x="4" y="11" width="8" height="4" fill="#fff" stroke="#a3273b"/></svg>862 415 2738</li>
    <li><svg viewBox="0 0 16 16" aria-hidden="true"><rect x="1" y="3" width="14" height="10"/><path d="M1 3l7 6 7-6" fill="none" stroke="#fff" stroke-width="1.4"/></svg>name@fernhollowair.example</li>
  </ul>

  <p class="address">PO box 518<br>Brightwater NJ 07912<br>www.FernhollowAirLLC.example</p>
</section>

</body>
</html>
```